Business Card Design Project

I require a business card with the following information on them for various different people;
name
m:
f:
e:
I have a logo already and will attached that. We are in the construction industry. I require something clean and simple but eye catching at the same time. You can use another colour with our logo if you like and you can style the logo as well if you wish. I am open.
Also it needs to be front and back design.
Industry/Entity Type
Construction
Requirements
Must have
- Logo, name, mobile, fax and email address.
Front and back design

```html
<!DOCTYPE html>
<html lang="en">
<head>
<meta charset="utf-8">
<title>Harrowfield Developments – Business Cards</title>
<link rel="stylesheet" href="https://fonts.googleapis.com/css2?family=Source+Sans+3:wght@400;600;700&display=swap">
<style>
  :root {
    --page-bg: #ece9e4;
    --card-white: #ffffff;
    --card-edge: #4a4a4a;
    --green-light: #b2d35a;
    --green-mid: #7cc04a;
    --green-deep: #4fae46;
    --rule-dark: #3a3a3a;
    --silver-light: #f4f4f5;
    --silver-dark: #c4c5c8;
    --text-white: #ffffff;
  }
  * { box-sizing: border-box; margin: 0; padding: 0; }
  html, body {
    width: 1200px;
    height: 757px;
    overflow: hidden;
    background: var(--page-bg);
    font-family: "Source Sans 3", Arial, sans-serif;
  }
  .canvas { position: relative; width: 1200px; height: 757px; }

  .card {
    position: absolute;
    width: 512px;
    height: 292px;
    background: var(--card-white);
    border: 1px solid var(--card-edge);
    overflow: hidden;
  }
  .card--front { left: 65px; top: 60px; }
  .card--back { left: 623px; top: 61px; }
  .card--silver {
    left: 342px; top: 402px; width: 514px; height: 293px;
    background: linear-gradient(100deg, var(--silver-light) 0%, #e3e4e6 55%, var(--silver-dark) 100%);
  }

  .brand {
    position: absolute;
    left: 0; right: 0;
    display: flex;
    align-items: center;
    justify-content: center;
    gap: 12px;
    white-space: nowrap;
  }
  .brand__mark {
    flex: none;
    width: 24px; height: 24px;
    background: var(--green-deep);
  }
  .brand__name {
    font-weight: 400;
    font-size: 30px;
    line-height: 1;
    color: var(--green-deep);
  }

  .card--front .brand { top: 84px; }
  .card--back .brand { top: 131px; }

  .front__rule {
    position: absolute;
    left: 0; right: 0; top: 190px;
    height: 2px;
    background: var(--rule-dark);
  }
  .front__band {
    position: absolute;
    left: 0; right: 0; top: 196px; bottom: 0;
    background: linear-gradient(90deg, var(--green-light) 0%, var(--green-mid) 60%, var(--green-deep) 100%);
  }
  .front__pointer { position: absolute; left: 0; top: 44px; }
  .holder {
    position: absolute;
    left: 57px; top: 44px;
    font-size: 16px;
    font-weight: 700;
    color: var(--text-white);
  }
  .front__divider {
    position: absolute;
    left: 218px; top: 16px;
    width: 1px; height: 70px;
    background: rgba(255,255,255,0.8);
  }
  .contact {
    position: absolute;
    left: 240px; top: 20px;
    list-style: none;
    font-size: 12.5px;
    line-height: 22px;
    color: var(--text-white);
  }
  .contact__label { display: inline-block; width: 36px; }

  .silver__band {
    position: absolute;
    left: 148px; top: 0; bottom: 0;
    width: 70px;
    background: linear-gradient(180deg, var(--green-light) 0%, var(--green-deep) 100%);
  }
  .card--silver .brand {
    left: 258px; right: 20px;
    top: 190px;
    justify-content: flex-start;
  }
  .card--silver .brand__name {
    font-size: 30px;
    line-height: 1.05;
    white-space: normal;
    width: 200px;
  }
</style>
</head>
<body>
<main class="canvas">

  <section class="card card--front" aria-label="Card front with contact details">
    <div class="brand">
      <span class="brand__mark"></span>
      <span class="brand__name">Harrowfield Developments</span>
    </div>
    <div class="front__rule"></div>
    <div class="front__band">
      <svg class="front__pointer" width="18" height="24" viewBox="0 0 18 24" aria-hidden="true">
        <polygon points="0,0 18,12 0,24" fill="#3a3a3a"/>
      </svg>
      <p class="holder">Your Name , Title</p>
      <div class="front__divider"></div>
      <ul class="contact">
        <li><span class="contact__label">Call</span>: +91 12345 67890</li>
        <li><span class="contact__label">Fax</span>: +91 12345 67890</li>
        <li>Email : harrowfield@xyzmail.com</li>
      </ul>
    </div>
  </section>

  <section class="card card--back" aria-label="Card back with brand name">
    <div class="brand">
      <span class="brand__mark"></span>
      <span class="brand__name">Harrowfield Developments</span>
    </div>
  </section>

  <section class="card card--silver" aria-label="Alternative silver card">
    <div class="silver__band"></div>
    <div class="brand">
      <span class="brand__name">Harrowfield Developments</span>
    </div>
  </section>

</main>
</body>
</html>
```